Luxury Wine Label for New Startup Winery

We need a wine label for our new winery startup. We have worked with a local designer but do not feel the resulting label / logo have the elevation required to present our brand as a luxury wine. Our winery is called "Quailbrook Vineyards" and we are focused on extremely high quality hand crafted artisan and estate wines from the Pacific Northwest.
We would like to see designs that utilize a tree line, or other imagery that represents the "Quailbrook" part of our company name. Another interesting feature could be wood grain.
A logo will be required based on your design so please design with this in mind:
This logo should be consistent with the wine bottle label design, and should be representative of our high end exclusive wine while giving a sense of place (Oregon/ Pacific Northwest.)
I will supply an image of the design we received from our local designer, PLEASE NOTE: in general we do like wood grain and tree line concepts but feel the execution was poorly done.
ATTN: Logo design should be suitable for use on: Bottles (Red wine/rose/white wine), Bussiness cards, vehicle signage, business signage, etc
P.S.:
If you have a design that is not outside the box we are still interested in seeing it.
Label is for a burgundy style bottle with a label height of 3.5 - 4" and a width of 3.5-4"
any label <= 4"x4" and >=3.5"x3.5" will be acceptable:
HOWEVER Width should be greater than or equal to height due to the bottle format
Target Market(s)
Wine enthusiasts with adequate discretionary budgets to afford $100 bottles of wine.
Industry/Entity Type
Wine / Winery
Requirements
Must have
- A sense of luxury, a feel of exclusivity, and a theme consistent with our product and brand name
Nice to have
- Tree line, wood grain or other wood themes. Serif fonts
Should not have
- anything cheesy, off topic, hard to read script fonts or anything that makes the label hard to read from a few feet away or too busy

```html
<!DOCTYPE html>
<html lang="en">
<head>
<meta charset="utf-8">
<title>Quailbrook Vineyards – Wine Labels</title>
<link rel="stylesheet" href="https://fonts.googleapis.com/css2?family=Cinzel:wght@400;700;900&display=swap">
<style>
  :root {
    --tan: #c49a67;
    --tan-light: #d8b88f;
    --tan-deep: #b78a57;
    --cream: #f3ece2;
    --ink: #0b0b0b;
    --ink-soft: #1c1915;
    --paper: #f4f4f4;
  }
  * { margin: 0; padding: 0; box-sizing: border-box; }
  html, body { width: 1200px; height: 3333px; overflow: hidden; background: var(--paper); }
  .sheet { position: relative; width: 1200px; height: 3333px; }

  /* Label box: all geometry in label units (1em = 1/100 of label width) */
  .label {
    position: absolute;
    width: 100em; height: 100em;
    font-family: "Cinzel", serif;
    overflow: hidden;
  }
  .label__rule-top, .label__rule-bottom, .label__divider {
    position: absolute; left: 0; width: 100%;
  }
  .label__rule-top { top: 0; height: 1.8em; }
  .label__rule-bottom { bottom: 0; height: 1.8em; }
  .label__grain-upper { position: absolute; left: 0; top: 1.8em; width: 100%; height: 56.9em; }
  .label__divider { top: 58.7em; height: 1.8em; }
  .label__grain-lower { position: absolute; left: 0; top: 60.5em; width: 100%; height: 37.7em; }

  .label__emblem {
    position: absolute; left: 50%; top: 7.5em;
    width: 29em; height: 29em; margin-left: -14.5em;
    border-radius: 50%;
    border: 0.6em solid var(--ink);
  }

  /* Text rows: wrapper positioned in label units, inner text sized separately */
  .label__row {
    position: absolute; left: 0; width: 100%;
    height: 10em;
    display: flex; align-items: center; justify-content: center;
    white-space: nowrap;
  }
  .label__row span { display: block; line-height: 1; }

  .row-brand { top: 40.6em; }
  .row-brand span { font-size: 10em; font-weight: 900; letter-spacing: 0.03em; color: var(--ink); }
  .row-sub { top: 47em; }
  .row-sub span { font-size: 3.8em; font-weight: 700; letter-spacing: 1.9em; margin-right: -1.9em; color: var(--ink); }

  .row-variety { top: 67.4em; }
  .row-variety span { font-size: 17em; font-weight: 400; letter-spacing: 0.02em; }
  .row-vintage { top: 81em; }
  .row-vintage span { font-size: 4.2em; font-weight: 400; }
  .row-region { top: 87.7em; }
  .row-region span { font-size: 4.2em; font-weight: 400; letter-spacing: 0.06em; }

  /* Dark variant: light upper, black lower, tan trim */
  .label--dark { border-left: 0.5em solid var(--tan); border-right: 0.5em solid var(--tan); }
  .label--dark .label__rule-top,
  .label--dark .label__rule-bottom,
  .label--dark .label__divider { background: var(--tan); }
  .label--dark .label__grain-upper {
    background: linear-gradient(100deg, var(--cream) 0%, #e4cfb3 30%, var(--cream) 55%, #e2cbac 80%, var(--cream) 100%);
  }
  .label--dark .label__grain-lower {
    background: linear-gradient(100deg, var(--ink) 0%, var(--ink-soft) 35%, var(--ink) 60%, var(--ink-soft) 85%, var(--ink) 100%);
  }
  .label--dark .row-variety span,
  .label--dark .row-vintage span,
  .label--dark .row-region span { color: var(--tan); }

  /* Tan variant: tan upper and lower, black trim */
  .label--tan .label__rule-top,
  .label--tan .label__rule-bottom,
  .label--tan .label__divider { background: var(--ink); }
  .label--tan .label__grain-upper {
    background: linear-gradient(100deg, var(--tan-light) 0%, #ead8c0 28%, var(--tan) 50%, #e4ceb1 75%, var(--tan-light) 100%);
  }
  .label--tan .label__grain-lower {
    background: linear-gradient(100deg, var(--tan) 0%, var(--tan-deep) 40%, var(--tan) 70%, var(--tan-deep) 100%);
  }
  .label--tan .row-variety span,
  .label--tan .row-vintage span,
  .label--tan .row-region span { color: var(--ink); }

  .label--lg { font-size: 5.33px; }
  .label--md { font-size: 3.42px; }
  .label--sm { font-size: 3.08px; }

  .pos-a { left: 44px; top: 124px; }
  .pos-b { left: 624px; top: 124px; }
  .pos-c { left: 180px; top: 1517px; }
  .pos-d { left: 699px; top: 1517px; }
  .pos-e { left: 197px; top: 2785px; }
  .pos-f { left: 716px; top: 2785px; }
</style>
</head>
<body>
<main class="sheet">

  <section class="label label--dark label--lg pos-a">
    <div class="label__rule-top"></div>
    <div class="label__grain-upper" role="img" aria-label="Tan wood grain pattern on white"></div>
    <div class="label__emblem"></div>
    <div class="label__row row-brand"><span>QUAILBROOK</span></div>
    <div class="label__row row-sub"><span>VINEYARDS</span></div>
    <div class="label__divider"></div>
    <div class="label__grain-lower" role="img" aria-label="Dark wood grain pattern on black"></div>
    <div class="label__row row-variety"><span>SYRAH</span></div>
    <div class="label__row row-vintage"><span>2024</span></div>
    <div class="label__row row-region"><span>WILLAMETTE VALLEY</span></div>
    <div class="label__rule-bottom"></div>
  </section>

  <section class="label label--tan label--lg pos-b">
    <div class="label__rule-top"></div>
    <div class="label__grain-upper" role="img" aria-label="White wood grain pattern on tan"></div>
    <div class="label__emblem"></div>
    <div class="label__row row-brand"><span>QUAILBROOK</span></div>
    <div class="label__row row-sub"><span>VINEYARDS</span></div>
    <div class="label__divider"></div>
    <div class="label__grain-lower" role="img" aria-label="Subtle wood grain pattern on tan"></div>
    <div class="label__row row-variety"><span>ROSÉ</span></div>
    <div class="label__row row-vintage"><span>2025</span></div>
    <div class="label__row row-region"><span>WILLAMETTE VALLEY</span></div>
    <div class="label__rule-bottom"></div>
  </section>

  <section class="label label--tan label--md pos-c">
    <div class="label__rule-top"></div>
    <div class="label__grain-upper" role="img" aria-label="White wood grain pattern on tan"></div>
    <div class="label__emblem"></div>
    <div class="label__row row-brand"><span>QUAILBROOK</span></div>
    <div class="label__row row-sub"><span>VINEYARDS</span></div>
    <div class="label__divider"></div>
    <div class="label__grain-lower" role="img" aria-label="Subtle wood grain pattern on tan"></div>
    <div class="label__row row-variety"><span>ROSÉ</span></div>
    <div class="label__row row-vintage"><span>2025</span></div>
    <div class="label__row row-region"><span>WILLAMETTE VALLEY</span></div>
    <div class="label__rule-bottom"></div>
  </section>

  <section class="label label--dark label--md pos-d">
    <div class="label__rule-top"></div>
    <div class="label__grain-upper" role="img" aria-label="Tan wood grain pattern on white"></div>
    <div class="label__emblem"></div>
    <div class="label__row row-brand"><span>QUAILBROOK</span></div>
    <div class="label__row row-sub"><span>VINEYARDS</span></div>
    <div class="label__divider"></div>
    <div class="label__grain-lower" role="img" aria-label="Dark wood grain pattern on black"></div>
    <div class="label__row row-variety"><span>ROSÉ</span></div>
    <div class="label__row row-vintage"><span>2024</span></div>
    <div class="label__row row-region"><span>WILLAMETTE VALLEY</span></div>
    <div class="label__rule-bottom"></div>
  </section>

  <section class="label label--dark label--sm pos-e">
    <div class="label__rule-top"></div>
    <div class="label__grain-upper" role="img" aria-label="Tan wood grain pattern on white"></div>
    <div class="label__emblem"></div>
    <div class="label__row row-brand"><span>QUAILBROOK</span></div>
    <div class="label__row row-sub"><span>VINEYARDS</span></div>
    <div class="label__divider"></div>
    <div class="label__grain-lower" role="img" aria-label="Dark wood grain pattern on black"></div>
    <div class="label__row row-variety"><span>SYRAH</span></div>
    <div class="label__row row-vintage"><span>2024</span></div>
    <div class="label__row row-region"><span>WILLAMETTE VALLEY</span></div>
    <div class="label__rule-bottom"></div>
  </section>

  <section class="label label--tan label--sm pos-f">
    <div class="label__rule-top"></div>
    <div class="label__grain-upper" role="img" aria-label="White wood grain pattern on tan"></div>
    <div class="label__emblem"></div>
    <div class="label__row row-brand"><span>QUAILBROOK</span></div>
    <div class="label__row row-sub"><span>VINEYARDS</span></div>
    <div class="label__divider"></div>
    <div class="label__grain-lower" role="img" aria-label="Subtle wood grain pattern on tan"></div>
    <div class="label__row row-variety"><span>SYRAH</span></div>
    <div class="label__row row-vintage"><span>2025</span></div>
    <div class="label__row row-region"><span>WILLAMETTE VALLEY</span></div>
    <div class="label__rule-bottom"></div>
  </section>

</main>
</body>
</html>
```